Christian Media Company Website

I am looking to design an easy to follow, sleek, creative website for my Christian video Bible study platform. On this platform you will be able to sign up to have access to dozens of free high-quality video Bible studies. With that being said There will be a total of 3 pages needed.

First, I will need the home page. This should contain all critical information to inform the customer. The design should be easy to follow, professional, and creative. I will post to some websites I like, if you just copy the website in your design will be removed immediately.

Secondly, we will need a landing Bible study page for people to look through the Bible studies to select one. I have uploaded Study images below with the aspect ratio I want for the design (for each Bible study image). There should be 2 sections Topical studies and Doctrinal Studies (with series under each section). I would like for people to be able to slide left or right through the studies under each category.

Lastly, we will need a video series page. This page needs to have the video they are watching, a playlist of the other videos, as well as a place to put the speaker's image and description. We will have studies that they can download so please make a place for this.

I will upload our color in the files along with our logo! Looking forward to seeing what you all will come up with!

Websites I like :
https://lanternvale.org/
https://www.quillharborfilms.org/
https://www.dunmorel.com/
https://tessavint.org/

Target Market(s)

Christians

Industry/Entity Type

Christian Video Design

Coding

Coded - Design and coding required

Number of Pages Required

3 page

Font styles to use
Sans Serif

Colors
00AB8E
00BBA5
67D7C9
C6EFE9
E9F9F6

Requirements
Should not have
• Pre-Used Templates

```html
<!DOCTYPE html>
<html lang="en">
<head>
<meta charset="utf-8">
<title>Kindred Path – Home</title>
<link rel="stylesheet" href="https://fonts.googleapis.com/css2?family=Saira+Semi+Condensed:wght@500;600&family=Arimo:wght@400;700&display=swap">
<style>
:root{
  --green:#00ab8e;
  --teal:#2cc2ac;
  --mint:#67d7c9;
  --pale:#e9f9f6;
  --ink:#2b2b2b;
  --grey:#777;
  --board:#efefef;
  --footer:#1d1d1d;
  --white:#fff;
}
*{box-sizing:border-box;margin:0;padding:0}
html,body{width:741px;height:1200px;overflow:hidden;background:var(--board)}
body{position:relative;font-family:"Arimo",Arial,sans-serif}
.page{position:absolute;top:29.4px;width:706px;height:2325px;background:var(--white);transform:scale(.4902);transform-origin:0 0;overflow:hidden;box-shadow:0 0 6px rgba(0,0,0,.15)}
.page--home{left:20.6px}
.page--modal{left:380.8px}
.abs{position:absolute}
.head{font-family:"Saira Semi Condensed","Arial Narrow",sans-serif;font-weight:600;text-transform:uppercase}
.fill{position:absolute}

/* hero */
.hero-band{left:0;top:0;width:399px;height:377px;background:var(--green)}
.brand{left:66px;top:10px;color:var(--white);font-size:18px;line-height:21px}
.nav{left:413px;top:27px;display:flex;gap:15px;font-size:8px;font-weight:700;color:var(--ink)}
.nav .is-active{color:var(--green);font-weight:400}
.hero-media{left:308px;top:60px;width:398px;height:276px;background:radial-gradient(ellipse at 30% 75%,#6a5440 0,transparent 45%),radial-gradient(ellipse at 80% 20%,#5a4a3c 0,transparent 50%),linear-gradient(135deg,#1d2a2c,#2a2622 60%,#3a2e24)}
.play{left:500px;top:166px;width:56px;height:56px}
.hero-title{left:65px;top:128px;width:230px;white-space:nowrap;color:var(--white);font-size:20px;line-height:29px}
.hero-text{left:65px;top:198px;width:228px;color:var(--white);font-size:8.5px;line-height:15px}
.btn-outline{left:65px;top:257px;width:92px;height:32px;border:1.5px solid var(--white);color:var(--white);font-size:9px;display:flex;align-items:center;justify-content:center}

/* about */
.section-title{left:0;width:706px;text-align:center;font-size:19px;color:var(--ink)}
.section-title span{color:var(--green)}
.rule{left:341px;width:24px;height:2px;background:var(--green)}
.about-text{left:143px;top:466px;width:420px;text-align:center;font-size:7.5px;line-height:16px;color:var(--grey)}
.poster{top:578px;width:136px;height:214px;background:var(--white);padding:5px;box-shadow:0 0 4px rgba(0,0,0,.15)}
.poster div{width:100%;height:100%}

/* studies band */
.band-left{left:0;top:834px;width:352px;height:184px;background:var(--green)}
.band-right{left:352px;top:834px;width:354px;height:184px;background:var(--teal)}
.band-copy{width:240px;text-align:center;color:var(--white);font-size:10.5px;line-height:17px}
.pill{height:30px;border:1.5px solid var(--white);border-radius:15px;color:var(--white);font-size:9.5px;display:flex;align-items:center;justify-content:center}

/* featured */
.tile{width:185px;height:137px;border-radius:4px;display:flex;align-items:center;justify-content:center;color:var(--white);font-size:17px;text-shadow:0 1px 3px rgba(0,0,0,.5)}
.tile.is-selected{border:3px solid var(--green)}

/* blog */
.blog-bg{left:0;top:1587px;width:706px;height:334px;background:#f6f6f6}
.card{top:1663px;width:275px;height:213px;background:var(--white);border:1px solid #e2e2e2}
.card-media{height:130px;position:relative}
.card-date{position:absolute;left:0;bottom:0;height:20px;width:88px;background:var(--green);color:var(--white);font-size:7.5px;line-height:20px;padding-left:10px;clip-path:polygon(0 0,86% 0,100% 100%,0 100%)}
.card-title{margin:18px 12px 0;font-size:9px;color:var(--ink);font-family:"Saira Semi Condensed","Arial Narrow",sans-serif;font-weight:500}
.card-text{margin:9px 12px 0;font-size:7.5px;line-height:15px;color:var(--grey)}
.card-text b{color:var(--green)}

/* newsletter */
.connect{left:0;top:1921px;width:706px;height:181px;background:var(--teal)}
.connect-title{top:1951px;left:0;width:706px;text-align:center;color:var(--white);font-size:20px}
.connect-text{top:1990px;left:143px;width:420px;text-align:center;color:var(--white);font-size:7.5px;line-height:15px}
.subscribe{left:140px;top:2031px;width:426px;height:33px;border-radius:17px;background:var(--white);overflow:hidden;display:flex}
.subscribe span{flex:1;font-size:8px;color:#555;padding-left:18px;line-height:33px}
.subscribe b{width:74px;background:#262626;color:var(--white);font-size:9px;text-align:center;line-height:33px}

/* footer */
.footer{left:0;top:2102px;width:706px;height:223px;background:var(--footer)}
.foot-brand{left:76px;top:2148px;color:var(--green);font-size:20px;line-height:25px}
.vline{top:2135px;width:1px;height:80px;background:#3a3a3a}
.foot-label{font-size:10.5px;line-height:14px;color:var(--white)}
.foot-value{font-size:7.5px;color:var(--white);font-weight:700;line-height:14px}
.social{top:2189px;width:24px;height:24px;border:1.5px solid var(--white);border-radius:50%}
.hline{left:66px;top:2243px;width:574px;height:1px;background:#333}
.foot-nav{top:2263px;font-size:8px;color:var(--white);font-weight:700}
.copyright{top:2290px;left:0;width:706px;text-align:center;font-size:8px;color:var(--white)}

/* modal */
.modal{left:171px;top:1225px;width:495px;height:388px;background:var(--white);border-radius:8px;box-shadow:0 2px 12px rgba(0,0,0,.2)}
.modal-title{left:0;top:32px;width:495px;text-align:center;color:var(--green);font-size:17px}
.modal-text{left:55px;top:60px;width:385px;text-align:center;font-size:7.5px;line-height:15px;color:var(--grey)}
.modal-meta{left:0;top:115px;width:495px;text-align:center;font-size:7.5px;line-height:15px;color:var(--green)}
.modal-media{left:45px;top:160px;width:405px;height:193px;background:radial-gradient(ellipse at 70% 40%,#f2c27a 0,transparent 55%),linear-gradient(120deg,#3d4a57 0,#8a7060 40%,#e0a860 75%,#c98a45)}
</style>
</head>
<body>

<!-- HOME: default state -->
<section class="page page--home">
  <div class="abs hero-band"></div>
  <div class="abs brand head">Kindred<br>Path</div>
  <nav class="abs nav"><span class="is-active">HOME</span><span>ABOUT US</span><span>EVENTS</span><span>VIDEO</span><span>CONTACT</span></nav>
  <div class="fill hero-media" role="img" aria-label="Worship crowd with raised hands in warm stage light"></div>
  <svg class="abs play" viewBox="0 0 56 56"><circle cx="28" cy="28" r="26.5" fill="none" stroke="#fff" stroke-width="2.5"/><path d="M22 18 L38 28 L22 38Z" fill="#fff"/></svg>
  <h1 class="abs hero-title head">Christian Video<br>Bible Study Platform</h1>
  <p class="abs hero-text">Sed ut perspiciatis unde omnis iste natus error sit volu ptatem accusantium doloremque laudantium, ipsaque inventore veritatis et quasi architecto</p>
  <div class="abs btn-outline head">Watch Video</div>

  <h2 class="abs section-title head" style="top:420px">About <span>Kindred Path</span></h2>
  <div class="abs rule" style="top:453px"></div>
  <p class="abs about-text">Sed ut perspiciatis unde omnis iste natus error sit voluptatem accusantium doloremque laudantium, totam rem aperiam, eaque ipsa quae ab illo inventore veritatis et quasi architecto beatae vitae dicta sunt explicabo. Nemo enim ipsam voluptatem quia voluptas sit aspernatur aut odit aut fugit, sed quia consequuntur magni dolores eos qui ratione voluptatem sequi nesciunt. Neque porro quisquam est, qui dolorem ipsum quia dolor sit amet, consectetur, adipisci modi tempora incidunt ut labore et dolore magnam aliquam quaerat voluptatem.</p>
  <div class="abs poster" style="left:65px"><div role="img" aria-label="Study poster with a speaker in a garden" style="background:linear-gradient(#7a8a62,#3c4030 55%,#1e2026)"></div></div>
  <div class="abs poster" style="left:211px"><div role="img" aria-label="Study poster with a speaker overlooking hills" style="background:linear-gradient(#d9d7d0,#a7a59c 50%,#5c5a55)"></div></div>
  <div class="abs poster" style="left:357px"><div role="img" aria-label="Study poster with a speaker in a red shirt" style="background:linear-gradient(#4c4a3c,#c76662 55%,#8a4d4a)"></div></div>
  <div class="abs poster" style="left:503px"><div role="img" aria-label="Study poster with a speaker in dark tones" style="background:linear-gradient(#5a5a5a,#262626 55%,#111)"></div></div>

  <div class="abs band-left"></div><div class="abs band-right"></div>
  <p class="abs band-copy head" style="left:55px;top:880px">Sed ut perspiciatis unde omnis iste natus error sit voluptatem</p>
  <div class="abs pill head" style="left:116px;top:934px;width:116px">Topical Studies</div>
  <p class="abs band-copy head" style="left:420px;top:880px">Sed ut perspiciatis unde omnis iste natus error sit voluptatem</p>
  <div class="abs pill head" style="left:477px;top:934px;width:126px">Doctrinal Studies</div>

  <h2 class="abs section-title head" style="top:1043px">Featured <span>Video</span></h2>
  <div class="abs tile head is-selected" style="left:65px;top:1100px;background:linear-gradient(135deg,#3c4a5a,#b0704a 50%,#e0a050)" role="img" aria-label="Open book in golden light">Three Gospels</div>
  <div class="abs tile head" style="left:260px;top:1100px;background:linear-gradient(135deg,#8a8c90,#5a5650 60%,#3a3430)" role="img" aria-label="Group reading together">Acts</div>
  <div class="abs tile head" style="left:455px;top:1100px;background:linear-gradient(135deg,#6a5a4a,#4a3a2c 60%,#2a2420)" role="img" aria-label="Hands holding an open Bible">Bible Studies</div>
  <div class="abs tile head" style="left:65px;top:1252px;background:linear-gradient(135deg,#7a6a60,#b08070 55%,#5a4a44)" role="img" aria-label="Hands on an open book">Books</div>
  <div class="abs tile head" style="left:260px;top:1252px;background:linear-gradient(#c08040,#e0a050 50%,#5a3a2a)" role="img" aria-label="Raised hands at sunset">James</div>
  <div class="abs tile head" style="left:455px;top:1252px;background:linear-gradient(135deg,#6a5a50,#8a7a6a 50%,#4a3a30)" role="img" aria-label="Wooden cross on a Bible">Other Letters</div>
  <div class="abs tile head" style="left:65px;top:1404px;background:radial-gradient(circle at 60% 40%,#6a6040,#1e2a24 65%)" role="img" aria-label="Glowing hands in the dark">Christian</div>
  <div class="abs tile head" style="left:260px;top:1404px;background:linear-gradient(135deg,#2a3430,#4a3a30 55%,#1a1e1c)" role="img" aria-label="Worship gathering">Church Order</div>
  <div class="abs tile head" style="left:455px;top:1404px;background:linear-gradient(135deg,#3a4448,#6a5040 50%,#2a2a2a)" role="img" aria-label="Hands joined in prayer">Online Trainning</div>

  <div class="abs blog-bg"></div>
  <h2 class="abs section-title head" style="top:1608px">Latest <span>Blog</span></h2>
  <div class="abs rule" style="top:1641px"></div>
  <article class="abs card" style="left:66px"><div class="card-media" role="img" aria-label="Person praying at sunrise" style="background:linear-gradient(#d9cfc0,#e8c090 50%,#3a3028)"><span class="card-date">02 MARCH 2022</span></div><h3 class="card-title">SED UT PERSPICIATIS UNDE OMNIS</h3><p class="card-text">Nemo enim ipsam voluptatem quia voluptas sit aspernatur aut eos qui ratione voluptatem sequi nesciunt. <b>READ MORE</b></p></article>
  <article class="abs card" style="left:365px"><div class="card-media" role="img" aria-label="Group studying Bibles around a table" style="background:linear-gradient(135deg,#5a5450,#3a3430 50%,#6a6460)"><span class="card-date">02 MARCH 2022</span></div><h3 class="card-title">SED UT PERSPICIATIS UNDE OMNIS</h3><p class="card-text">Nemo enim ipsam voluptatem quia voluptas sit aspernatur aut eos qui ratione voluptatem sequi nesciunt. <b>READ MORE</b></p></article>

  <div class="abs connect"></div>
  <h2 class="abs connect-title head">Stay Connected</h2>
  <p class="abs connect-text">Sed ut perspiciatis unde omnis iste natus error sit voluptatem accusantium doloremque laudantium, totam rem ab illo inventore veritatis et quasi architecto beatae vitae dicta sunt explicabo.</p>
  <div class="abs subscribe"><span>Enter Your Email :</span><b>SUBMIT</b></div>

  <footer class="abs footer"></footer>
  <div class="abs foot-brand head">Kindred<br>Path</div>
  <div class="abs vline" style="left:262px"></div>
  <div class="abs vline" style="left:455px"></div>
  <svg class="abs" style="left:289px;top:2143px" width="11" height="14" viewBox="0 0 11 14"><path d="M5.5 13 C2 8.5 1 6.5 1 5 A4.5 4.5 0 0 1 10 5 C10 6.5 9 8.5 5.5 13Z" fill="none" stroke="#fff"/><circle cx="5.5" cy="5" r="1.6" fill="none" stroke="#fff"/></svg>
  <div class="abs" style="left:311px;top:2141px"><div class="foot-label head">ADDRESS</div><div class="foot-value">#254 Lorem Ipsum Dummy<br>Lorem Ipsum</div></div>
  <div class="abs social" style="left:311px"></div>
  <div class="abs social" style="left:342px"></div>
  <svg class="abs" style="left:477px;top:2144px" width="12" height="12" viewBox="0 0 12 12"><path d="M2 1 L4.5 1 L5.5 4 L4 5 C5 7 6 8 7.5 8.5 L8.5 7 L11 8 L11 10.5 C6 11 1 6 2 1Z" fill="none" stroke="#fff"/></svg>
  <div class="abs" style="left:500px;top:2141px"><div class="foot-label head">PHONE</div><div class="foot-value">000-555-0142</div></div>
  <svg class="abs" style="left:477px;top:2185px" width="13" height="10" viewBox="0 0 13 10"><rect x=".5" y=".5" width="12" height="9" fill="none" stroke="#fff"/><path d="M.5 .5 L6.5 5.5 L12.5 .5" fill="none" stroke="#fff"/></svg>
  <div class="abs" style="left:500px;top:2180px"><div class="foot-label head">EMAIL</div><div class="foot-value">hello@kindredpath.org</div></div>
  <div class="abs hline"></div>
  <span class="abs foot-nav" style="left:183px">HOME</span><span class="abs foot-nav" style="left:252px">ABOUT US</span><span class="abs foot-nav" style="left:339px">EVENTS</span><span class="abs foot-nav" style="left:415px">VIDEO</span><span class="abs foot-nav" style="left:485px">CONTACT</span>
  <p class="abs copyright">Kindred Path © 2022.All Rights Reserved.</p>
</section>

<!-- HOME: study preview open -->
<section class="page page--modal">
  <div class="abs hero-band"></div>
  <div class="abs brand head">Kindred<br>Path</div>
  <nav class="abs nav"><span class="is-active">HOME</span><span>ABOUT US</span><span>EVENTS</span><span>VIDEO</span><span>CONTACT</span></nav>
  <div class="fill hero-media" role="img" aria-label="Worship crowd with raised hands in warm stage light"></div>
  <svg class="abs play" viewBox="0 0 56 56"><circle cx="28" cy="28" r="26.5" fill="none" stroke="#fff" stroke-width="2.5"/><path d="M22 18 L38 28 L22 38Z" fill="#fff"/></svg>
  <h1 class="abs hero-title head">Christian Video<br>Bible Study Platform</h1>
  <p class="abs hero-text">Sed ut perspiciatis unde omnis iste natus error sit volu ptatem accusantium doloremque laudantium, ipsaque inventore veritatis et quasi architecto</p>
  <div class="abs btn-outline head">Watch Video</div>

  <h2 class="abs section-title head" style="top:420px">About <span>Kindred Path</span></h2>
  <div class="abs rule" style="top:453px"></div>
  <p class="abs about-text">Sed ut perspiciatis unde omnis iste natus error sit voluptatem accusantium doloremque laudantium, totam rem aperiam, eaque ipsa quae ab illo inventore veritatis et quasi architecto beatae vitae dicta sunt explicabo. Nemo enim ipsam voluptatem quia voluptas sit aspernatur aut odit aut fugit, sed quia consequuntur magni dolores eos qui ratione voluptatem sequi nesciunt. Neque porro quisquam est, qui dolorem ipsum quia dolor sit amet, consectetur, adipisci modi tempora incidunt ut labore et dolore magnam aliquam quaerat voluptatem.</p>
  <div class="abs poster" style="left:65px"><div role="img" aria-label="Study poster with a speaker in a garden" style="background:linear-gradient(#7a8a62,#3c4030 55%,#1e2026)"></div></div>
  <div class="abs poster" style="left:211px"><div role="img" aria-label="Study poster with a speaker overlooking hills" style="background:linear-gradient(#d9d7d0,#a7a59c 50%,#5c5a55)"></div></div>
  <div class="abs poster" style="left:357px"><div role="img" aria-label="Study poster with a speaker in a red shirt" style="background:linear-gradient(#4c4a3c,#c76662 55%,#8a4d4a)"></div></div>
  <div class="abs poster" style="left:503px"><div role="img" aria-label="Study poster with a speaker in dark tones" style="background:linear-gradient(#5a5a5a,#262626 55%,#111)"></div></div>

  <div class="abs band-left"></div><div class="abs band-right"></div>
  <p class="abs band-copy head" style="left:55px;top:880px">Sed ut perspiciatis unde omnis iste natus error sit voluptatem</p>
  <div class="abs pill head" style="left:116px;top:934px;width:116px">Topical Studies</div>
  <p class="abs band-copy head" style="left:420px;top:880px">Sed ut perspiciatis unde omnis iste natus error sit voluptatem</p>
  <div class="abs pill head" style="left:477px;top:934px;width:126px">Doctrinal Studies</div>

  <h2 class="abs section-title head" style="top:1043px">Featured <span>Video</span></h2>
  <div class="abs tile head is-selected" style="left:65px;top:1100px;background:linear-gradient(135deg,#3c4a5a,#b0704a 50%,#e0a050)" role="img" aria-label="Open book in golden light">Three Gospels</div>
  <div class="abs tile head" style="left:260px;top:1100px;background:linear-gradient(135deg,#8a8c90,#5a5650 60%,#3a3430)" role="img" aria-label="Group reading together">Acts</div>
  <div class="abs tile head" style="left:455px;top:1100px;background:linear-gradient(135deg,#6a5a4a,#4a3a2c 60%,#2a2420)" role="img" aria-label="Hands holding an open Bible">Bible Studies</div>
  <div class="abs tile head" style="left:65px;top:1252px;background:linear-gradient(135deg,#7a6a60,#b08070 55%,#5a4a44)" role="img" aria-label="Hands on an open book">Books</div>
  <div class="abs tile head" style="left:65px;top:1404px;background:radial-gradient(circle at 60% 40%,#6a6040,#1e2a24 65%)" role="img" aria-label="Glowing hands in the dark">Christian</div>

  <div class="abs blog-bg"></div>
  <h2 class="abs section-title head" style="top:1608px">Latest <span>Blog</span></h2>
  <div class="abs rule" style="top:1641px"></div>
  <article class="abs card" style="left:66px"><div class="card-media" role="img" aria-label="Person praying at sunrise" style="background:linear-gradient(#d9cfc0,#e8c090 50%,#3a3028)"><span class="card-date">02 MARCH 2022</span></div><h3 class="card-title">SED UT PERSPICIATIS UNDE OMNIS</h3><p class="card-text">Nemo enim ipsam voluptatem quia voluptas sit aspernatur aut eos qui ratione voluptatem sequi nesciunt. <b>READ MORE</b></p></article>
  <article class="abs card" style="left:365px"><div class="card-media" role="img" aria-label="Group studying Bibles around a table" style="background:linear-gradient(135deg,#5a5450,#3a3430 50%,#6a6460)"><span class="card-date">02 MARCH 2022</span></div><h3 class="card-title">SED UT PERSPICIATIS UNDE OMNIS</h3><p class="card-text">Nemo enim ipsam voluptatem quia voluptas sit aspernatur aut eos qui ratione voluptatem sequi nesciunt. <b>READ MORE</b></p></article>

  <div class="abs modal">
    <h3 class="abs modal-title head">Three Gospels</h3>
    <p class="abs modal-text">Sed ut perspiciatis unde omnis iste natus error sit voluptatem accusantium doloremque laudantium, totam rem aperiam, eaque ipsa quae ab illo inventore veritatis et quasi architecto beatae vitae dicta sunt sed quia consequuntur magni dolores eos qui ratione voluptatem sequi nesciunt</p>
    <p class="abs modal-meta">Story : &nbsp;Background of the book of Three Gospels &nbsp; | &nbsp; Location: &nbsp;Kingdom of Judea<br>Time: &nbsp;Circa 5-1 BC &nbsp;| &nbsp;Primary Scriptures: ThreeGospels &nbsp;1</p>
    <div class="abs modal-media" role="img" aria-label="Open Bible with a small cross in golden light"></div>
    <svg class="abs" style="left:224px;top:232px" width="50" height="50" viewBox="0 0 50 50"><circle cx="25" cy="25" r="23.5" fill="none" stroke="#fff" stroke-width="2"/><path d="M20 16 L34 25 L20 34Z" fill="none" stroke="#fff" stroke-width="2"/></svg>
  </div>

  <div class="abs connect"></div>
  <h2 class="abs connect-title head">Stay Connected</h2>
  <p class="abs connect-text">Sed ut perspiciatis unde omnis iste natus error sit voluptatem accusantium doloremque laudantium, totam rem ab illo inventore veritatis et quasi architecto beatae vitae dicta sunt explicabo.</p>
  <div class="abs subscribe"><span>Enter Your Email :</span><b>SUBMIT</b></div>

  <footer class="abs footer"></footer>
  <div class="abs foot-brand head">Kindred<br>Path</div>
  <div class="abs vline" style="left:262px"></div>
  <div class="abs vline" style="left:455px"></div>
  <svg class="abs" style="left:289px;top:2143px" width="11" height="14" viewBox="0 0 11 14"><path d="M5.5 13 C2 8.5 1 6.5 1 5 A4.5 4.5 0 0 1 10 5 C10 6.5 9 8.5 5.5 13Z" fill="none" stroke="#fff"/><circle cx="5.5" cy="5" r="1.6" fill="none" stroke="#fff"/></svg>
  <div class="abs" style="left:311px;top:2141px"><div class="foot-label head">ADDRESS</div><div class="foot-value">#254 Lorem Ipsum Dummy<br>Lorem Ipsum</div></div>
  <div class="abs social" style="left:311px"></div>
  <div class="abs social" style="left:342px"></div>
  <svg class="abs" style="left:477px;top:2144px" width="12" height="12" viewBox="0 0 12 12"><path d="M2 1 L4.5 1 L5.5 4 L4 5 C5 7 6 8 7.5 8.5 L8.5 7 L11 8 L11 10.5 C6 11 1 6 2 1Z" fill="none" stroke="#fff"/></svg>
  <div class="abs" style="left:500px;top:2141px"><div class="foot-label head">PHONE</div><div class="foot-value">000-555-0142</div></div>
  <svg class="abs" style="left:477px;top:2185px" width="13" height="10" viewBox="0 0 13 10"><rect x=".5" y=".5" width="12" height="9" fill="none" stroke="#fff"/><path d="M.5 .5 L6.5 5.5 L12.5 .5" fill="none" stroke="#fff"/></svg>
  <div class="abs" style="left:500px;top:2180px"><div class="foot-label head">EMAIL</div><div class="foot-value">hello@kindredpath.org</div></div>
  <div class="abs hline"></div>
  <span class="abs foot-nav" style="left:183px">HOME</span><span class="abs foot-nav" style="left:252px">ABOUT US</span><span class="abs foot-nav" style="left:339px">EVENTS</span><span class="abs foot-nav" style="left:415px">VIDEO</span><span class="abs foot-nav" style="left:485px">CONTACT</span>
  <p class="abs copyright">Kindred Path © 2022.All Rights Reserved.</p>
</section>

</body>
</html>
```